Orvane Group Business Card

Building Management company based in Sydney, Australia. We provide onsite management for commercial and residential buildings.
I would like a sophisticated minimalist design that indicates that we provide a high-end service. I would like a silver or metal look background or something similar.
The business card should have:
Name
Title
email
Office Phone
Mobile
Address
Website
The services that we provide should be prominent:
Building Management - Concierge - Caretaking - Cleaning

```html
<!DOCTYPE html>
<html lang="en">
<head>
<meta charset="utf-8">
<title>Orvane Group Business Card</title>
<link href="https://fonts.googleapis.com/css2?family=Open+Sans:wght@400;600;700;800&display=swap" rel="stylesheet">
<style>
  :root {
    --backdrop: #2a2a2c;
    --metal-light: #f4f4f5;
    --metal-mid: #d9dadc;
    --metal-dark: #c2c4c7;
    --brand-blue: #2f74c0;
    --brand-blue-deep: #245fa3;
    --ink: #1c1c1e;
    --ink-soft: #3a3a3d;
    --band-black: #141416;
    --white: #ffffff;
  }
  * { margin: 0; padding: 0; box-sizing: border-box; }
  html, body {
    width: 1200px; height: 852px; overflow: hidden;
    background: var(--backdrop);
    font-family: "Open Sans", Arial, sans-serif;
  }
  .stage { position: relative; width: 1200px; height: 852px; }

  .card {
    position: absolute;
    width: 520px; height: 300px;
    border-radius: 22px;
    overflow: hidden;
    background:
      repeating-linear-gradient(100deg, rgba(255,255,255,0.35) 0 1px, rgba(0,0,0,0.03) 1px 3px),
      linear-gradient(135deg, var(--metal-light) 0%, var(--metal-mid) 40%, var(--metal-light) 65%, var(--metal-dark) 100%);
  }
  .card--front { left: 110px; top: 100px; }
  .card--back  { left: 570px; top: 450px; }

  .wordmark {
    display: flex; align-items: center; gap: 12px;
    font-weight: 800; color: var(--ink);
    letter-spacing: 1px; text-transform: uppercase;
  }
  .wordmark__square { width: 16px; height: 16px; background: var(--brand-blue); }

  .card--front .wordmark {
    position: absolute; left: 0; right: 0; top: 112px;
    justify-content: center; font-size: 38px;
  }
  .front-web {
    position: absolute; left: 0; right: 0; top: 196px;
    display: flex; align-items: center; justify-content: center; gap: 16px;
    font-size: 13px; letter-spacing: 3px; color: var(--ink-soft);
  }
  .front-web__rule { width: 50px; height: 2px; background: var(--brand-blue); }
  .front-services {
    position: absolute; left: 0; right: 0; top: 232px;
    text-align: center; font-size: 11px; font-weight: 600;
    letter-spacing: 1.5px; text-transform: uppercase; color: var(--brand-blue);
  }

  .card--back .wordmark {
    position: absolute; left: 30px; top: 130px; font-size: 24px; gap: 9px;
  }
  .card--back .wordmark__square { width: 12px; height: 12px; }
  .back-divider {
    position: absolute; left: 262px; top: 30px; width: 1px; height: 170px;
    background: rgba(0,0,0,0.08);
  }
  .contact { position: absolute; left: 282px; top: 36px; color: var(--ink); }
  .contact__name { font-size: 17px; font-weight: 700; color: var(--brand-blue); }
  .contact__title { font-size: 10px; color: var(--ink-soft); margin-top: 2px; }
  .contact__list { list-style: none; margin-top: 20px; font-size: 12px; line-height: 1.35; }
  .contact__list li { display: flex; align-items: flex-start; gap: 8px; }
  .contact__list svg { width: 11px; height: 11px; margin-top: 3px; flex: none; fill: var(--ink); }
  .contact__spacer { width: 11px; flex: none; }
  .contact__address { margin-top: 4px; }

  .back-bands { position: absolute; left: 0; top: 0; width: 520px; height: 300px; }
  .back-web {
    position: absolute; right: 22px; top: 222px;
    font-size: 13px; color: var(--white);
  }
  .back-web span { color: var(--brand-blue); }
</style>
</head>
<body>
<main class="stage">

  <section class="card card--front" aria-label="Card front">
    <div class="wordmark"><span class="wordmark__square"></span><span>Orvane Group</span></div>
    <div class="front-web">
      <span class="front-web__rule"></span>
      <span>www.orvanegroup.co.uk</span>
      <span class="front-web__rule"></span>
    </div>
    <p class="front-services">Building Management · Concierge · Caretaking · Cleaning</p>
  </section>

  <section class="card card--back" aria-label="Card back">
    <svg class="back-bands" viewBox="0 0 520 300" aria-hidden="true">
      <polygon points="0,288 372,258 368,300 0,300" fill="var(--brand-blue)"/>
      <polygon points="0,294 370,272 368,300 0,300" fill="var(--brand-blue-deep)"/>
      <polygon points="372,204 520,204 520,300 358,300" fill="var(--band-black)"/>
    </svg>

    <div class="wordmark"><span class="wordmark__square"></span><span>Orvane Group</span></div>
    <div class="back-divider"></div>

    <div class="contact">
      <p class="contact__name">Your Long Name</p>
      <p class="contact__title">Managing Director</p>
      <ul class="contact__list">
        <li><svg viewBox="0 0 12 12"><path d="M2 1h3l1 3-2 1a7 7 0 0 0 3 3l1-2 3 1v3c-6 0-9-3-9-9z"/></svg>00.00.00.0000</li>
        <li><svg viewBox="0 0 12 12"><path d="M3 0h6v12H3zM4 1v9h4V1z" fill-rule="evenodd"/></svg>00.00.00.0000</li>
        <li><svg viewBox="0 0 12 12"><path d="M0 2h12v8H0zM1 3l5 4 5-4z" fill-rule="evenodd"/></svg>yourname@yourwebsite.com</li>
        <li class="contact__address"><span class="contact__spacer"></span>Your Commercial or office address<br>in just two line with pincode</li>
      </ul>
    </div>

    <p class="back-web">www.<span>yourwebsite.com</span></p>
  </section>

</main>
</body>
</html>
```